20 year old business card needs re-design

We need to redesign our corporate business card look. We need something that appears more modern, eye catchy but professional.

Target Market(s)

manufacturing industry

Industry/Entity Type

Manufacturer

Contact Information for Business Card

One side can have the logo. Other side can have contact information.

Font styles to use
Serif

Colors
3277b5
33b8a4
ffffff

Requirements
Must have
• Eye catchy - need to standout from the crowd. company logo cannot change. Full name, job title, phone number and email address.
Should not have
• Fax, business address is not necessary.

```html
<!DOCTYPE html>
<html lang="en">
<head>
<meta charset="utf-8">
<title>Norvale Industrial Business Card</title>
<link href="https://fonts.googleapis.com/css2?family=Tinos:wght@400;700&display=swap" rel="stylesheet">
<style>
  :root {
    --brand-blue: #1b4f9c;
    --accent-teal: #33b8a4;
    --ink: #222222;
    --card: #ffffff;
    --backdrop: #e4e6ea;
  }
  * { box-sizing: border-box; margin: 0; padding: 0; }
  html, body {
    width: 1200px; height: 880px; overflow: hidden;
    background: var(--backdrop);
    font-family: "Tinos", "Times New Roman", serif;
    color: var(--ink);
  }
  .sheet {
    width: 1200px; height: 880px;
    display: flex; flex-direction: column; align-items: center; justify-content: center;
    gap: 44px;
  }
  .card {
    position: relative;
    width: 640px; height: 366px;
    background: var(--card);
    box-shadow: 0 6px 18px rgba(0,0,0,.18);
    overflow: hidden;
  }
  .band {
    position: absolute; left: 0; right: 0; bottom: 0;
    height: 56px;
    background: var(--brand-blue);
    border-top: 5px solid var(--accent-teal);
    display: flex; align-items: center;
    color: #fff;
  }
  .wordmark {
    display: flex; flex-direction: column; align-items: center;
    color: var(--ink); font-weight: 700; line-height: 1;
  }
  .wordmark-name { font-size: 64px; letter-spacing: -1px; }
  .wordmark-sub { font-size: 15px; letter-spacing: 14px; margin-top: 8px; padding-left: 14px; }

  /* Front */
  .card-front .wordmark { position: absolute; left: 0; right: 0; top: 104px; }
  .card-front .band { justify-content: flex-start; padding-left: 140px; }
  .web { font-weight: 700; font-size: 17px; }

  /* Back */
  .card-back .wordmark { position: absolute; left: 0; right: 0; top: 40px; }
  .card-back .wordmark-name { font-size: 54px; }
  .card-back .wordmark-sub { font-size: 13px; letter-spacing: 12px; }
  .person { position: absolute; right: 258px; top: 160px; text-align: right; }
  .person-name { color: var(--brand-blue); font-weight: 700; font-size: 22px; }
  .person-title { font-size: 15px; margin-top: 2px; }
  .divider { position: absolute; left: 398px; top: 164px; width: 2px; height: 46px; background: var(--accent-teal); }
  .contact { position: absolute; left: 416px; top: 162px; font-size: 15px; line-height: 1.5; }
  .contact b { color: var(--brand-blue); }
  .about { position: absolute; left: 40px; top: 232px; font-size: 14px; line-height: 1.3; }
  .about .cert { margin-top: 8px; }
  .card-back .band { justify-content: flex-end; padding-right: 60px; }
  .locations { font-size: 15px; letter-spacing: .5px; }
</style>
</head>
<body>
<main class="sheet">
  <section class="card card-front" aria-label="Card front">
    <div class="wordmark">
      <span class="wordmark-name">Norvale</span>
      <span class="wordmark-sub">INDUSTRIAL</span>
    </div>
    <div class="band"><span class="web">NorvaleIndustrial.com</span></div>
  </section>

  <section class="card card-back" aria-label="Card back">
    <div class="wordmark">
      <span class="wordmark-name">Norvale</span>
      <span class="wordmark-sub">INDUSTRIAL</span>
    </div>
    <div class="person">
      <p class="person-name">Daniel Marsh</p>
      <p class="person-title">Senior Project Manager</p>
    </div>
    <div class="divider"></div>
    <div class="contact">
      <p><b>Main:</b> 555-014-2200 xt 201</p>
      <p>daniel@norvaleindustrial.com</p>
    </div>
    <div class="about">
      <p>International manufacturing solutions</p>
      <p>for OEM customers in North America</p>
      <p class="cert">TS16949 &amp; ISO9001 Certified Facilities</p>
    </div>
    <div class="band"><span class="locations">Offices &amp; Warehousing: USA - Taiwan - Mexico</span></div>
  </section>
</main>
</body>
</html>
```